New Coffee Shop business card

We are opening our new coffee shop and are needing business cards to take with us on February 6th to Atlanta, Ga to a show.

We will be offering the following menu type items:

coffee
teas
espresso
frappes
smoothies

sandwiches
soups
salads
pastries
ice cream

Our shop is in a rural country-side area and we would like to convey that feel in our shop. In addition to the cafe we will also be selling gifts and furniture and other home decor. Much of this merchandise will be rescued, refurbished or repurposed which is also a core value of what we are all about.

We have a company logo we would like incorporated into the design.

We will also provide files that have the elements of the logo which may also be useful in the design of the card.

Since we are not open yet we need one slightly altered version of the card as well as the final product which states "Opening in the summer 2015"

Target Market(s)

moderate to slightly upscale and folksy.

Industry/Entity Type

Coffee Shop

Contact Information for Business Card

Fern Kettle Coffee
name
address
phone number
email

Card

Font styles to use
Sans Serif

Requirements
Must have
• Must include Logo
• Must include information on menu.
• Must include information on our merchandise sales as described inthe project description.
• Color scheme to complement the logo
Nice to have
• The following descriptions
• "We are also selling gifts, furniture, and other home decoration."
• "We rescue, refurbish, and repurpose old furniture so it can live again."

```html
<!DOCTYPE html>
<html lang="en">
<head>
<meta charset="utf-8">
<title>Fern Kettle Coffee – Business Card</title>
<link href="https://fonts.googleapis.com/css2?family=Questrial&display=swap" rel="stylesheet">
<style>
  :root {
    --page-bg: #8f8f8f;
    --card-dark: #2a2727;
    --card-dark-mid: #3c3938;
    --photo-grey: #8a8887;
    --card-light: #f2f2f2;
    --photo-light: #d9d9d9;
    --ink-light: #ffffff;
    --ink-dark: #3a3a3a;
    --shadow: rgba(0, 0, 0, 0.35);
  }
  * { box-sizing: border-box; margin: 0; padding: 0; }
  html, body { width: 1200px; height: 1000px; overflow: hidden; }
  body {
    background: var(--page-bg);
    font-family: "Questrial", "Century Gothic", sans-serif;
    position: relative;
  }
  .card {
    position: absolute;
    left: 220px;
    width: 760px;
    height: 434px;
    overflow: hidden;
    box-shadow: 0 10px 24px var(--shadow);
  }
  /* Front */
  .card-front { top: 40px; background: var(--card-dark); }
  .card-front .photo {
    position: absolute; inset: 0 auto 0 0; width: 52%;
    background: linear-gradient(90deg, var(--photo-grey) 0%, var(--card-dark-mid) 55%, var(--card-dark) 100%);
  }
  .card-front .brand {
    position: absolute; top: 44px; right: 44px;
    display: flex; align-items: center; gap: 10px;
    color: var(--ink-light); font-size: 20px;
  }
  .brand .mark { width: 16px; height: 16px; background: currentColor; }
  .card-front .contact {
    position: absolute; right: 44px; top: 170px;
    text-align: right; color: var(--ink-light);
    font-size: 27px; line-height: 1.45; letter-spacing: 0.5px;
  }
  /* Back */
  .card-back { top: 520px; background: var(--card-light); }
  .card-back .photo {
    position: absolute; inset: 0;
    background: radial-gradient(ellipse at 55% 35%, var(--photo-light) 0%, var(--card-light) 60%, #e6e6e6 100%);
  }
  .card-back .content {
    position: absolute; inset: 0;
    color: var(--ink-dark); text-align: center;
  }
  .card-back .brand {
    position: absolute; top: 30px; left: 50%; transform: translateX(-50%);
    display: flex; align-items: center; gap: 8px;
    font-size: 16px; color: var(--ink-dark); white-space: nowrap;
  }
  .menu-title { position: absolute; top: 72px; left: 410px; font-size: 17px; }
  .menu-col {
    position: absolute; list-style: none;
    font-size: 17px; line-height: 1.3;
  }
  .menu-drinks { top: 100px; left: 250px; width: 120px; }
  .menu-food { top: 118px; left: 430px; width: 140px; }
  .notes {
    position: absolute; left: 0; right: 0; top: 270px;
    font-size: 18px; line-height: 1.6;
  }
</style>
</head>
<body>
  <section class="card card-front" aria-label="Card front">
    <div class="photo" role="img" aria-label="Photo of an espresso machine pouring coffee"></div>
    <div class="brand"><span class="mark"></span><span>Fern Kettle</span></div>
    <div class="contact">
      <p>Your Name Your Name</p>
      <p>Address, Country, State, Zip 000000</p>
      <p>000 0000 0000</p>
      <p>your_email@company.com</p>
    </div>
  </section>

  <section class="card card-back" aria-label="Card back">
    <div class="photo" role="img" aria-label="Photo of a cup of coffee on a saucer with coffee beans"></div>
    <div class="content">
      <div class="brand"><span class="mark"></span><span>Fern Kettle</span></div>
      <p class="menu-title">Menu:</p>
      <ul class="menu-col menu-drinks">
        <li>Coffee</li><li>Teas</li><li>Espresso</li><li>Frappes</li><li>Smoothies</li>
      </ul>
      <ul class="menu-col menu-food">
        <li>Sandwiches</li><li>Soups</li><li>Salads</li><li>Pastries</li><li>Ice cream</li>
      </ul>
      <div class="notes">
        <p>Opening in the summer 2015.</p>
        <p>We are also selling gifts, furniture, and other home decoration.</p>
        <p>We rescue, refurbish, and repurpose old furniture so it can live again.</p>
      </div>
    </div>
  </section>
</body>
</html>
```